Professional Services - letterhead / business cards

The company (velmora partners) will provide services to Investment Funds and large investors in Spain. I have recently chosen a logo that I am attaching.

I would like a simple stationary design that i could use as letter head, business cards and "with compliments" cards.

I am not quite sure which color I will mostly use for the logo, in the email signature I will probably lean towards the white background and grey letters. I am attaching my favourite options.

Target Market(s)

Large Multinationals, Investment funds and Law firms

Industry/Entity Type

Business

Requirements
Must have
• my details are:
Luis R. Abadal
Velmora Partners S.L.
Casa de Torrelumbre
Calle de Vientoalto 27
28014 Madrid
T: +34 (91) 387-2265
M: +34 (646) 819-054
e-mail: labadal@velmorapartners.com

```html
<!DOCTYPE html>
<html lang="en">
<head>
<meta charset="UTF-8">
<title>Velmora Partners – Business Card</title>
<link rel="stylesheet" href="https://fonts.googleapis.com/css2?family=Mulish:wght@300;400&display=swap">
<style>
  :root {
    --backdrop: #e6e6e8;
    --card: #ffffff;
    --ink: #2f2b6e;
    --shadow: rgba(0, 0, 0, 0.18);
  }
  * { margin: 0; padding: 0; box-sizing: border-box; }
  html, body {
    width: 1200px;
    height: 900px;
    overflow: hidden;
    background: var(--backdrop);
  }
  .business-card {
    position: absolute;
    left: 150px;
    top: 193px;
    width: 900px;
    height: 514px;
    background: var(--card);
    box-shadow: 0 12px 40px var(--shadow);
    font-family: "Mulish", "Helvetica Neue", Arial, sans-serif;
    color: var(--ink);
  }
  .brand-name {
    position: absolute;
    left: 118px;
    top: 70px;
    font-size: 44px;
    font-weight: 300;
    letter-spacing: 0.5px;
  }
  .holder {
    position: absolute;
    left: 96px;
    top: 214px;
  }
  .holder-name {
    font-size: 24px;
    font-weight: 400;
    letter-spacing: 2.5px;
    text-transform: uppercase;
  }
  .holder-company {
    font-size: 17px;
    font-weight: 400;
    margin-top: 2px;
  }
  .contact {
    position: absolute;
    left: 420px;
    top: 276px;
    font-size: 18px;
    font-weight: 400;
    line-height: 1.25;
  }
  .contact-row { display: flex; }
  .contact-label { width: 32px; }
  .address {
    margin-top: 22px;
    line-height: 1.3;
  }
</style>
</head>
<body>
  <div class="business-card">
    <div class="brand-name">velmora partners</div>

    <div class="holder">
      <div class="holder-name">Luis R. Abadal</div>
      <div class="holder-company">Velmora Partners S.L.</div>
    </div>

    <div class="contact">
      <div class="contact-row"><span class="contact-label">T</span><span>+34 (91) 387-2265</span></div>
      <div class="contact-row"><span class="contact-label">M</span><span>+34 (646) 819-054</span></div>
      <div class="contact-row"><span class="contact-label">E</span><span>labadal@velmorapartners.com</span></div>
      <div class="address">
        Casa de Torrelumbre<br>
        Calle de Vientoalto 27,<br>
        28014 Madrid
      </div>
    </div>
  </div>
</body>
</html>
```